Refresh Application User Interface

Brightmoor wishes to update the look of its business applications. Two representative forms are shown below. Please note, we are not considering changes in functionality or usability. Our goal is a cleaner, more contemporary design.

Industry/Entity Type

Business

```html
<!DOCTYPE html>
<html lang="en">
<head>
<meta charset="utf-8">
<title>Brightmoor – Purchase Order</title>
<link rel="stylesheet" href="https://fonts.googleapis.com/css2?family=Open+Sans:wght@400;600;700;800&display=swap">
<style>
:root{
  --page:#e8e8ea;
  --topbar:#5b5b5b;
  --green:#8cc63f;
  --blue:#0b3f91;
  --ink:#333;
  --muted:#555;
  --panel:#f8f6f6;
  --line:#c9c9c9;
  --field-line:#bdbdbd;
  --link:#0b3f91;
}
*{box-sizing:border-box;margin:0;padding:0}
html,body{width:1200px;height:930px;overflow:hidden;background:var(--page);font-family:"Open Sans",sans-serif;color:var(--ink)}
.canvas{width:1200px;height:930px;overflow:hidden;position:relative}
.stage{width:1500px;height:1162px;transform:scale(.8);transform-origin:0 0;position:relative}
.abs{position:absolute}
.app{left:98px;top:66px;width:1301px;height:1011px;background:#fff;box-shadow:0 1px 4px rgba(0,0,0,.12)}
.topbar{left:0;top:0;width:1301px;height:35px;background:var(--topbar);color:#fff;font-size:14.5px;display:flex;align-items:center}
.topbar .item{height:35px;display:flex;align-items:center;padding:0 18px;gap:8px}
.topbar .sep{border-right:1px solid #777}
.topbar .right{margin-left:auto;display:flex}
.topbar .right .item{border-left:1px solid #777}
.mainnav{left:0;top:35px;width:1301px;height:66px;display:flex;align-items:center;font-size:13px;font-weight:700;letter-spacing:.3px;color:#444}
.mainnav a{color:inherit;text-decoration:none;display:flex;align-items:center;height:54px;margin-top:12px;padding:0 20px}
.mainnav a.active{background:var(--green);color:#fff;padding:0 15px}
.brand{position:absolute;right:18px;top:12px;font-size:38px;font-weight:800;color:var(--blue);letter-spacing:1px;display:flex;align-items:center;gap:8px}
.brand .mark{width:14px;height:14px;background:var(--green)}
.subnav{left:0;top:101px;width:1301px;height:36px;background:var(--green);display:flex;color:#fff;font-weight:700;font-size:14px;letter-spacing:.3px}
.subnav a{color:#fff;text-decoration:none;display:flex;align-items:center;padding:0 17px;border-right:1px solid rgba(255,255,255,.45)}
.subnav a:last-child{border-right:none}
.title{left:20px;top:162px;font-size:20px;font-weight:800;color:#555;letter-spacing:.3px}
.doc-tabs{left:963px;top:162px;height:43px;display:flex;font-size:13px;font-weight:700;color:#555}
.doc-tabs span{display:flex;align-items:center;padding:0 10px;gap:4px}
.doc-tabs span.active{background:var(--blue);color:#fff;padding:0 16px}
.ok{width:11px;height:11px}
.frame{left:118px;top:271px;width:1260px;height:782px;border:2px solid #dcdcdc;border-top:none}
.toolbar{left:118px;top:271px;width:1260px;height:35px;background:var(--blue);color:#fff;display:flex;align-items:center;font-size:14px;font-weight:600;padding-left:16px}
.toolbar .ico{width:20px;height:20px;margin-right:20px;display:flex;align-items:center}
.toolbar .act{display:flex;align-items:center;gap:5px;margin-left:26px}
.toolbar .act.dim{color:#8fa6cf;font-weight:400}
.toolbar .right{margin-left:auto;display:flex;padding-right:22px}
.panel{left:133px;top:320px;width:1227px;height:677px;background:var(--panel);border:1px solid #d6d6d6}
.panel-head{height:47px;border-bottom:1px solid #ddd;display:flex;align-items:center;padding:0 20px;font-size:15px}
.panel-head .order{font-weight:700;color:#444;width:420px}
.panel-head .hold{margin-left:auto;color:var(--link);text-decoration:underline;font-weight:600}
.lbl{font-size:16px;font-weight:700;color:#555}
.fld{background:#fff;border:1px solid var(--field-line);height:40px;display:flex;align-items:center;padding:0 12px;font-size:14.5px;color:#333}
.btn{background:var(--blue);color:#fff;font-size:12px;font-weight:700;letter-spacing:.6px;display:flex;align-items:center;justify-content:center}
.check{width:24px;height:24px;background:#fff;border:1px solid #aaa;display:flex;align-items:center;justify-content:center}
.tabs{left:156px;top:665px;width:1178px;height:300px;border:1px solid #c8c8c8;background:var(--panel)}
.tabbar{height:45px;background:#ededed;border-bottom:1px solid #cfcfcf;display:flex;font-size:15px}
.tabbar span{display:flex;align-items:center;padding:0 19px}
.tabbar span.active{background:var(--blue);color:#fff;padding:0 15px}
.f-lbl{font-size:15px;color:#333}
.sel{background:#fff;border:1px solid var(--field-line);width:178px;height:40px;display:flex;align-items:center;justify-content:space-between;padding:0 12px;font-size:14.5px}
.caret{width:0;height:0;border-left:5px solid transparent;border-right:5px solid transparent;border-top:6px solid #333}
.footer-note{left:118px;top:1015px;width:1260px;text-align:center;font-size:14.5px}
</style>
</head>
<body>
<div class="canvas"><div class="stage">
  <div class="abs app">
    <div class="abs topbar">
      <div class="item sep" style="padding-left:22px;width:229px">Logged in As Dana Reyes
        <svg width="14" height="14" viewBox="0 0 16 16"><circle cx="8" cy="8" r="5" fill="none" stroke="#fff" stroke-width="3.5" stroke-dasharray="2.2 1.6"/><circle cx="8" cy="8" r="3.2" fill="#fff"/><circle cx="8" cy="8" r="1.4" fill="#5b5b5b"/></svg></div>
      <div class="item" style="padding-left:20px">Current Role Administrator
        <svg width="14" height="14" viewBox="0 0 16 16"><circle cx="8" cy="8" r="7" fill="#fff"/><text x="8" y="12" font-size="11" font-weight="700" text-anchor="middle" fill="#5b5b5b" font-family="Open Sans,sans-serif">?</text></svg></div>
      <div class="right">
        <div class="item" style="border-left:none">Touch</div>
        <div class="item">New Tab</div>
        <div class="item">Help</div>
        <div class="item">Support</div>
        <div class="item">Log out</div>
      </div>
    </div>
    <nav class="abs mainnav">
      <a>HOME</a><a>eSOURCE</a><a class="active">eBUY</a><a>eREQUEST</a><a>eSELL</a><a style="padding:0 26px">eSTOCK</a><a style="padding:0 24px">ePLAN</a><a>PREFERENCES</a>
      <div class="brand"><span class="mark"></span>BRIGHTMOOR</div>
    </nav>
    <nav class="abs subnav">
      <a style="padding-left:20px">ORDERS</a><a>RECEIPTS</a><a>SHIPMENTS</a><a>INVOICES</a><a>PRICING</a><a>TABLES</a><a>REPORTS</a><a>INQUIRIES</a><a>PERIODIC TASKS</a><a>WORKFLOWS</a>
    </nav>
    <h1 class="abs title">PURCHASE ORDER</h1>
    <div class="abs doc-tabs">
      <span class="active">HEADER</span>
      <span style="padding-left:19px">LINES <svg class="ok" viewBox="0 0 12 12"><circle cx="6" cy="6" r="6" fill="#8cc63f"/><path d="M3 6l2 2 4-4" stroke="#fff" stroke-width="1.6" fill="none"/></svg></span>
      <span style="padding-left:15px">CHARGES</span>
      <span>NOTES <svg class="ok" viewBox="0 0 12 12"><circle cx="6" cy="6" r="6" fill="#8cc63f"/><path d="M3 6l2 2 4-4" stroke="#fff" stroke-width="1.6" fill="none"/></svg></span>
    </div>
  </div>

  <div class="abs frame"></div>
  <div class="abs toolbar">
    <span class="ico"><svg width="18" height="18" viewBox="0 0 18 18" fill="none" stroke="#fff" stroke-width="2"><rect x="2" y="2" width="7" height="5" rx="2.5" transform="rotate(45 5.5 4.5)"/><rect x="9" y="9" width="7" height="5" rx="2.5" transform="rotate(45 12.5 11.5)"/></svg></span>
    <span class="ico"><svg width="16" height="18" viewBox="0 0 16 18"><path d="M2 1h8l4 4v12H2z" fill="#fff"/><circle cx="9" cy="11" r="2.5" fill="none" stroke="#0b3f91" stroke-width="1.5"/><path d="M11 13l2 2" stroke="#0b3f91" stroke-width="1.5"/></svg></span>
    <span class="ico"><svg width="16" height="16" viewBox="0 0 16 16" fill="#fff"><circle cx="3" cy="8" r="2.5"/><circle cx="13" cy="3" r="2.5"/><circle cx="13" cy="13" r="2.5"/><path d="M3 8L13 3M3 8l10 5" stroke="#fff" stroke-width="1.6"/></svg></span>
    <span class="ico" style="margin-right:24px"><svg width="20" height="16" viewBox="0 0 20 16" fill="#fff"><path d="M1 2h6l2 2h7v3H5L1 14z"/><path d="M5 8h14l-4 7H1z"/></svg></span>
    <span class="ico"><svg width="18" height="18" viewBox="0 0 18 18"><circle cx="9" cy="9" r="8.5" fill="#7d97c7"/><text x="9" y="13.5" font-size="13" font-weight="700" text-anchor="middle" fill="#0b3f91" font-family="Open Sans,sans-serif">?</text></svg></span>
    <span style="display:flex;align-items:center;gap:8px"><svg width="12" height="14" viewBox="0 0 12 14"><path d="M1 0h7l4 4v10H1z" fill="#fff"/><path d="M3 7h6M3 10h6" stroke="#0b3f91" stroke-width="1.2"/></svg>Post Order</span>
    <div class="right">
      <span class="act dim"><svg width="13" height="13" viewBox="0 0 13 13" fill="none" stroke="#8fa6cf" stroke-width="1.8"><circle cx="5.5" cy="5.5" r="4"/><path d="M8.5 8.5l3.5 3.5"/></svg>Search</span>
      <span class="act dim"><svg width="11" height="11" viewBox="0 0 11 11" stroke="#8fa6cf" stroke-width="2.2"><path d="M5.5 0v11M0 5.5h11"/></svg>New</span>
      <span class="act"><svg width="12" height="11" viewBox="0 0 12 11" fill="none" stroke="#fff" stroke-width="2.4"><path d="M1 6l3.5 3.5L11 1"/></svg>Apply</span>
      <span class="act"><svg width="11" height="11" viewBox="0 0 11 11" stroke="#fff" stroke-width="2.6"><path d="M1 1l9 9M10 1l-9 9"/></svg>Delete</span>
      <span class="act"><svg width="16" height="13" viewBox="0 0 16 13" fill="#fff"><path d="M6 0L0 5l6 5V7c5 0 8 2 10 6 0-6-4-9-10-9z"/></svg>Back</span>
    </div>
  </div>

  <section class="abs panel">
    <div class="panel-head"><span class="order">Order&nbsp; #110051</span><span>Regular Purchase Order</span><span class="hold">Hold For Completion</span></div>
  </section>

  <span class="abs lbl" style="left:161px;top:405px">Ship From</span>
  <div class="abs fld" style="left:255px;top:396px;width:181px">1001</div>
  <span class="abs" style="left:453px;top:405px;font-size:15px">/</span>
  <div class="abs fld" style="left:473px;top:396px;width:44px">0</div>
  <div class="abs fld" style="left:543px;top:396px;width:450px;padding-left:14px">Harbor Supply Co</div>

  <span class="abs lbl" style="left:162px;top:469px">Address</span>
  <div class="abs fld" style="left:256px;top:456px;width:353px">14 Linden St</div>
  <div class="abs fld" style="left:637px;top:456px;width:353px"></div>
  <span class="abs" style="left:1004px;top:468px;font-size:14px;font-weight:600;color:var(--link)">DPV Unconfirmed</span>

  <span class="abs lbl" style="left:162px;top:521px">City</span>
  <div class="abs fld" style="left:256px;top:512px;width:353px">Ashford</div>
  <span class="abs lbl" style="left:636px;top:521px">State</span>
  <div class="abs fld" style="left:690px;top:512px;width:109px">MA</div>
  <div class="abs check" style="left:909px;top:520px"><svg width="14" height="12" viewBox="0 0 14 12" fill="none" stroke="#444" stroke-width="2.4"><path d="M1 6l4 4 8-9"/></svg></div>
  <span class="abs" style="left:947px;top:521px;font-size:15px">Accept</span>

  <span class="abs lbl" style="left:162px;top:580px">Zip</span>
  <div class="abs fld" style="left:256px;top:571px;width:133px">0172-4410</div>
  <span class="abs lbl" style="left:451px;top:580px">Country</span>
  <div class="abs fld" style="left:530px;top:571px;width:78px">US</div>
  <div class="abs btn" style="left:637px;top:577px;width:125px;height:32px">ADD CONTACT</div>

  <section class="abs tabs">
    <div class="tabbar"><span>Order Info</span><span class="active">Shipping</span><span style="padding-left:31px">Payment</span><span>Accounts</span><span>Totals / Approval</span></div>
  </section>

  <span class="abs f-lbl" style="left:192px;top:743px">Receive At *</span>
  <div class="abs sel" style="left:191px;top:770px">ALCH<i class="caret"></i></div>
  <span class="abs f-lbl" style="left:422px;top:743px">Carrier *</span>
  <div class="abs sel" style="left:421px;top:770px">SwiftFreight<i class="caret"></i></div>
  <span class="abs f-lbl" style="left:658px;top:743px">Express Service</span>
  <div class="abs sel" style="left:657px;top:770px"><span></span><i class="caret"></i></div>
  <span class="abs f-lbl" style="left:887px;top:743px">FOB</span>
  <div class="abs sel" style="left:886px;top:770px"><span></span><i class="caret"></i></div>
  <span class="abs f-lbl" style="left:1110px;top:743px">Order Ship Rule *</span>
  <div class="abs sel" style="left:1109px;top:770px">Partials<i class="caret"></i></div>

  <span class="abs f-lbl" style="left:192px;top:844px">Line Ship Rule *</span>
  <div class="abs sel" style="left:191px;top:871px">Partials<i class="caret"></i></div>
  <span class="abs f-lbl" style="left:422px;top:844px">Request Date</span>
  <div class="abs sel" style="left:421px;top:871px">01/07/2018<svg width="15" height="15" viewBox="0 0 15 15" fill="none" stroke="#444" stroke-width="1.3"><rect x="1" y="2.5" width="13" height="11.5"/><path d="M1 6h13M4 0.5v3M11 0.5v3M4.5 6v8M7.5 6v8M10.5 6v8M1 9h13M1 11.5h13"/></svg></div>
  <span class="abs f-lbl" style="left:658px;top:844px">Freight Terms</span>
  <div class="abs sel" style="left:657px;top:871px;padding-left:15px">Collect<i class="caret"></i></div>
  <span class="abs f-lbl" style="left:887px;top:844px">Freight Calc</span>
  <div class="abs sel" style="left:886px;top:871px"><span></span><i class="caret"></i></div>
  <span class="abs f-lbl" style="left:1110px;top:844px">Customer Ship to</span>
  <div class="abs fld" style="left:1109px;top:871px;width:109px;background:#f5f5f5;border-color:#ddd"></div>
  <span class="abs" style="left:1229px;top:880px;font-size:14px">/</span>
  <div class="abs fld" style="left:1249px;top:871px;width:40px;background:#f5f5f5;border-color:#ddd"></div>

  <p class="abs footer-note">Enter Property Values, and click apply</p>
</div></div>
</body>
</html>
```